National Water and Fire Restoration, Multi Surface Cleaning, Carpet Cleaning Business Needs a Websi

We need a new fresh website for our business. There are multiple services we offer and we need a fresh corporate website that represents us better. We start from cleaning carpet and tiles, to upholstery and curtains, to completely clean all contents and building materials after a fire, or completely dry out a home or business after a major or minor flood event. We are open to all concepts as we want to create a new look, maybe even logo, signage, vehicle signage, uniforms.
We are open to new colours etc.

Go to www.brightvaleclean.com.au for current logo and all other past ideas

Reason: I need to see more quality designs to sink my teeth into

Target Market(s)

The target market is everyone of all walks of life

Industry/Entity Type

Business

Number of Pages Required

3 page

Font styles to use
Sans Serif

Requirements
Must have
• Home page
• Services page
• Contact us page
• The rest is up to your imagination
• ***This is design only - NO CODING REQUIRED***
Nice to have
• Pictures

```html
<!DOCTYPE html>
<html lang="en">
<head>
<meta charset="utf-8">
<title>Brightvale Clean</title>
<link rel="stylesheet" href="https://fonts.googleapis.com/css2?family=Open+Sans:ital,wght@0,400;0,600;0,700;0,800;1,700;1,800&display=swap">
<style>
:root{
  --blue:#1b4f9e;
  --blue-dark:#12356d;
  --navy:#0f2c5a;
  --magenta:#c41e6a;
  --red:#e2262b;
  --grey:#f1f2f4;
  --line:#d9dce2;
  --text:#3a3f48;
  --white:#ffffff;
}
*{box-sizing:border-box;margin:0;padding:0}
html,body{width:761px;height:1200px;overflow:hidden;background:var(--white)}
body{font-family:"Open Sans",sans-serif;color:var(--text);font-size:10px}
.page{position:relative;width:761px;height:1200px;overflow:hidden;background:var(--white)}
.abs{position:absolute}

/* header */
.brand{left:60px;top:14px;display:flex;align-items:center;gap:10px}
.brand-dot{width:46px;height:46px;border-radius:50%;background:var(--blue)}
.brand-name{font-size:24px;font-weight:800;color:var(--blue);line-height:1;white-space:nowrap}
.phone{right:60px;top:10px;display:flex;align-items:center;gap:6px;font-size:15px;font-weight:700;color:var(--blue)}
.mission{right:60px;top:34px;text-align:right;color:var(--magenta);font-weight:700;font-size:10px;line-height:1.35}
.mission b{display:block;font-size:10px;letter-spacing:.5px}

/* nav */
.nav{left:80px;top:96px;width:600px;height:18px;display:flex;justify-content:space-between;align-items:center;border-bottom:2px solid var(--magenta)}
.nav a{font-size:8.5px;line-height:12px;color:var(--blue);text-decoration:none;padding:3px 7px;font-weight:600;white-space:nowrap}
.nav a.active{background:var(--magenta);color:var(--white)}

/* hero */
.hero{left:80px;top:116px;width:600px;height:255px;background:linear-gradient(135deg,#e9e2d8,#c9b9a4 55%,#8f7a66)}
.hero-caption{left:80px;top:332px;width:600px;height:28px;background:linear-gradient(90deg,rgba(27,79,158,.2),var(--blue) 30%,var(--blue) 70%,rgba(27,79,158,.2));color:var(--white);font-style:italic;font-weight:800;font-size:15px;text-align:center;line-height:28px;white-space:nowrap}
.dots{left:350px;top:378px;display:flex;gap:5px}
.dots span{width:6px;height:6px;border-radius:50%;background:#c4c8d0}
.dots span.on{background:var(--blue)}

/* service cards */
.card{top:395px;width:136px;height:195px;text-align:center}
.card-icon{width:34px;height:34px;border-radius:50%;border:3px solid var(--blue);background:var(--white);margin:0 auto 4px}
.card h3{font-size:11px;font-weight:800;font-style:italic;color:var(--red);line-height:1.2;height:30px}
.card-photo{width:136px;height:90px;margin-top:4px}
.btn{display:inline-block;background:var(--blue);color:var(--white);font-size:8.5px;font-weight:700;padding:3px 10px;border-radius:3px;margin-top:-8px;position:relative;white-space:nowrap}

/* reasons */
.reasons{left:80px;top:610px;width:160px;height:180px;background:linear-gradient(180deg,var(--blue),var(--blue-dark));color:var(--white);padding:10px}
.reasons-head{display:flex;align-items:center;gap:8px;margin-bottom:10px}
.reasons-num{width:26px;height:30px;background:var(--white);color:var(--blue);font-weight:800;font-size:22px;text-align:center;line-height:30px}
.reasons h2{font-size:20px;font-style:italic;font-weight:800}
.reasons li{list-style:none;font-size:8.5px;font-weight:600;margin-bottom:7px;display:flex;align-items:center;gap:5px;white-space:nowrap}
.reasons li::before{content:"";width:5px;height:5px;background:var(--white);border-radius:50%}

.schedule{left:255px;top:610px;width:150px;height:180px}
.schedule h2{color:var(--red);font-size:12px;font-weight:800;line-height:1.3;margin-bottom:8px}
.schedule-photo{width:150px;height:100px;background:linear-gradient(135deg,#dde6f2,#9fb3cd)}

.welcome{left:420px;top:610px;width:260px;height:180px}
.welcome-head{display:flex;align-items:center;gap:8px}
.welcome h2{color:var(--magenta);font-size:18px;font-style:italic;font-weight:800;white-space:nowrap}
.welcome-mark{font-size:12px;font-weight:800;color:var(--blue);display:flex;align-items:center;gap:4px;white-space:nowrap}
.welcome-mark i{width:14px;height:14px;border-radius:50%;background:var(--blue)}
.welcome-body{display:flex;gap:8px;margin-top:8px}
.welcome-photo{flex:0 0 95px;width:95px;height:120px;background:linear-gradient(160deg,#b8d4ea,#5e8fbd)}
.welcome p{font-size:7px;line-height:1.45;margin-bottom:5px}
.welcome .btn{margin-top:2px;float:right}

/* list / seal / offer */
.svc-list{left:80px;top:820px;width:210px}
.svc-list li{list-style:none;display:flex;align-items:center;gap:8px;height:40px;font-size:10px;font-weight:700;color:var(--magenta);white-space:nowrap}
.svc-icon{width:30px;height:24px;border-radius:4px;background:var(--blue)}
.seal{left:300px;top:810px;width:180px;height:180px}
.offer{left:490px;top:815px;width:190px;height:170px;background:linear-gradient(135deg,#f6f3ef,#d9cbbd);padding:14px}
.offer h2{color:var(--magenta);font-size:18px;font-style:italic;font-weight:800}
.offer p{font-size:8px;margin-top:4px;width:100px}
.offer .btn{margin-top:10px;background:var(--magenta)}

/* footer */
.footer{left:0;top:1000px;width:761px;height:180px;background:var(--navy);color:var(--white)}
.f-col h4{font-size:10px;font-weight:700;margin-bottom:6px;white-space:nowrap}
.f-links{left:80px;top:14px}
.f-links li{list-style:none;font-size:8px;line-height:1.55}
.f-news{left:190px;top:14px;width:150px}
.f-news p{font-size:7.5px;line-height:1.4;margin-bottom:6px}
.f-input{width:110px;height:14px;background:var(--white);font-size:7px;color:#888;padding:2px 4px}
.f-sub{margin-top:6px;display:inline-block;background:var(--white);color:var(--navy);font-size:7.5px;font-weight:700;padding:2px 8px}
.f-badge{left:380px;top:14px;width:130px;height:140px;background:var(--white);border-radius:4px}
.f-social{left:530px;top:14px;width:150px;height:140px;border:1px solid #3a5a8e;padding:10px;text-align:center}
.f-social h4{font-size:12px;font-weight:800;margin-bottom:6px}
.f-social p{font-size:7.5px;line-height:1.4}
.f-social .site{margin-top:10px;font-weight:700}
.copy{left:0;top:1180px;width:761px;height:20px;background:var(--blue-dark);color:var(--white);font-size:7.5px;text-align:center;line-height:20px}
</style>
</head>
<body>
<div class="page">

  <header>
    <div class="abs brand"><span class="brand-dot"></span><span class="brand-name">Brightvale Clean</span></div>
    <div class="abs phone">
      <svg width="14" height="14" viewBox="0 0 24 24"><path fill="#1b4f9e" d="M6.6 10.8a15 15 0 0 0 6.6 6.6l2.2-2.2c.3-.3.7-.4 1-.2 1.1.4 2.3.6 3.6.6.6 0 1 .4 1 1V20c0 .6-.4 1-1 1A17 17 0 0 1 3 4c0-.6.4-1 1-1h3.5c.6 0 1 .4 1 1 0 1.3.2 2.5.6 3.6.1.3 0 .7-.2 1z"/></svg>
      4000 1234
    </div>
    <div class="abs mission"><b>OUR MISSION</b>To Provide You With Most<br>Outstanding Service Experience Ever!</div>
  </header>

  <nav class="abs nav">
    <a class="active">Home</a><a>About Us</a><a>Services</a><a>Commercial</a><a>Schedule a Job</a><a>Referral Program</a><a>Contact Us</a><a>Links</a><a>Newsletter</a>
  </nav>

  <div class="abs hero" role="img" aria-label="Family relaxing together on a freshly cleaned carpet"></div>
  <div class="abs hero-caption">Professional Cleaners of Carpets, Rugs, Floors and Fine Fabrics</div>
  <div class="abs dots"><span class="on"></span><span></span><span></span></div>

  <section>
    <div class="abs card" style="left:80px">
      <div class="card-icon"></div>
      <h3>Storm, Flood &amp; Water<br>Damage Restoration</h3>
      <div class="card-photo" role="img" aria-label="Flooded living room" style="background:linear-gradient(135deg,#a9c2d8,#5a7d9c)"></div>
      <span class="btn">read more</span>
    </div>
    <div class="abs card" style="left:235px">
      <div class="card-icon"></div>
      <h3>Cleaning Water Damage<br>Carpet</h3>
      <div class="card-photo" role="img" aria-label="Technician extracting water from carpet" style="background:linear-gradient(135deg,#d7d1c8,#8c8072)"></div>
      <span class="btn">read more</span>
    </div>
    <div class="abs card" style="left:390px">
      <div class="card-icon"></div>
      <h3>Wood Floor Drying<br>Services</h3>
      <div class="card-photo" role="img" aria-label="Drying equipment on a wooden floor" style="background:linear-gradient(135deg,#d9a873,#8a5a2f)"></div>
      <span class="btn">read more</span>
    </div>
    <div class="abs card" style="left:544px">
      <div class="card-icon"></div>
      <h3>Fire Damage<br>Restoration</h3>
      <div class="card-photo" role="img" aria-label="Fire damaged room interior" style="background:linear-gradient(135deg,#7d6a5c,#2e2420)"></div>
      <span class="btn">read more</span>
    </div>
  </section>

  <section>
    <div class="abs reasons">
      <div class="reasons-head"><span class="reasons-num">6</span><h2>Reasons</h2></div>
      <ul>
        <li>Reputation</li><li>Experience</li><li>Education &amp; Certification</li><li>Cleaning Systems</li><li>First Class Customer Service</li><li>100% Money Back Guarantee</li>
      </ul>
    </div>
    <div class="abs schedule">
      <h2>Click Here To<br>Schedule Your<br>Cleaning Today...</h2>
      <div class="schedule-photo" role="img" aria-label="Service van and cleaning technician"></div>
    </div>
    <div class="abs welcome">
      <div class="welcome-head"><h2>Welcome To</h2><span class="welcome-mark"><i></i>Brightvale Clean</span></div>
      <div class="welcome-body">
        <div class="welcome-photo" role="img" aria-label="Cleaning technician at work"></div>
        <div>
          <p>Brightvale Clean is a professional, full service carpet, floor, fabric and restoration company serving homes and businesses across the region since 1996.</p>
          <p>At Brightvale Clean we take pride in our reputation, experience, education and guarantee. Our team is certified by a leading industry body.</p>
          <span class="btn">read more</span>
        </div>
      </div>
    </div>
  </section>

  <section>
    <ul class="abs svc-list">
      <li><span class="svc-icon"></span>Carpets &amp; Upholstery Cleaning</li>
      <li><span class="svc-icon" style="background:var(--red)"></span>Water Damage</li>
      <li><span class="svc-icon"></span>Tile &amp; Grout Cleaning</li>
      <li><span class="svc-icon" style="background:var(--magenta)"></span>Pest Control</li>
    </ul>
    <svg class="abs seal" viewBox="0 0 180 180" aria-label="Over 25 years">
      <circle cx="90" cy="90" r="78" fill="#e2262b"/>
      <circle cx="90" cy="90" r="64" fill="none" stroke="#ffffff" stroke-width="2"/>
      <text x="90" y="70" text-anchor="middle" fill="#fff" font-family="Open Sans, sans-serif" font-weight="800" font-size="16">OVER</text>
      <text x="90" y="118" text-anchor="middle" fill="#fff" font-family="Open Sans, sans-serif" font-weight="800" font-size="50">25</text>
      <text x="90" y="140" text-anchor="middle" fill="#fff" font-family="Open Sans, sans-serif" font-weight="700" font-size="11">YEARS</text>
    </svg>
    <div class="abs offer" role="img" aria-label="Smiling customer with introductory offer">
      <h2>Introductory<br>offer!</h2>
      <p>Ask about our first visit discount.</p>
      <span class="btn">Click Here</span>
    </div>
  </section>

  <footer class="abs footer">
    <div class="abs f-col f-links">
      <h4>Quick Links</h4>
      <ul><li>Home</li><li>About Us</li><li>Services</li><li>Contact us</li><li>Schedule a Job</li><li>Referral Program</li><li>Contact Us</li><li>Links</li><li>Newsletter</li></ul>
    </div>
    <div class="abs f-col f-news">
      <h4>Subscribe to Newsletter</h4>
      <p>Get Latest Updates By Entering Your Email Address</p>
      <div class="f-input">Email Address</div>
      <span class="f-sub">Subscribe</span>
    </div>
    <div class="abs f-badge" role="img" aria-label="Certified firm badge"></div>
    <div class="abs f-social">
      <h4>Follow Us Online</h4>
      <p>Join us online for news, offers and tips.</p>
      <p class="site">Brightvale Clean - Carpet Cleaning Services</p>
      <p>www.brightvaleclean.com.au</p>
    </div>
  </footer>
  <div class="abs copy">© 2024 Brightvale Clean. All Rights Reserved.</div>

</div>
</body>
</html>
```